Marwick Law Letterhead

We need a new letterhead design for a Law Firm. The address for the law firm is 1475 Calloway Street, Suite 210, Houston, Texas 77041. Phone Number: 832-361-9027; Fax Number: 832-614-7359. The logo is uploaded to the project.

```html
<!DOCTYPE html>
<html lang="en">
<head>
<meta charset="utf-8">
<title>Marwick Law Letterhead</title>
<link href="https://fonts.googleapis.com/css2?family=Arimo:wght@400;700&display=swap" rel="stylesheet">
<style>
  :root{
    --backdrop:#ececec;
    --paper:#f7f7f6;
    --ink:#2b2b2b;
    --navy:#1f2d5a;
    --accent:#c8202f;
    --rule:#c8202f;
  }
  html,body{margin:0;padding:0;overflow:hidden;}
  body{
    width:1200px;height:795px;
    background:var(--backdrop);
    display:flex;align-items:center;justify-content:center;
    font-family:"Arimo",Arial,sans-serif;
  }
  .letterhead{
    position:relative;
    width:527px;height:745px;
    background:var(--paper);
    box-shadow:0 2px 10px rgba(0,0,0,.12);
    color:var(--ink);
    box-sizing:border-box;
  }
  .brand{
    position:absolute;top:58px;left:0;right:0;
    display:flex;align-items:center;justify-content:center;gap:8px;
  }
  .brand-mark{width:14px;height:14px;background:var(--navy);}
  .brand-name{
    font-size:19px;font-weight:700;color:var(--navy);letter-spacing:.5px;
  }
  .brand-rule{
    position:absolute;top:86px;left:50%;width:120px;margin-left:-60px;
    height:1px;background:var(--rule);
  }
  .letter{
    position:absolute;top:225px;left:62px;right:62px;
    font-size:9px;line-height:1.45;
  }
  .salutation{font-size:12.5px;margin:0 0 14px;}
  .letter p.body{margin:0 0 14px;}
  .closing{margin:22px 0 6px;}
  .signature{
    display:block;width:80px;height:30px;
    background:linear-gradient(90deg,rgba(30,30,40,.18),rgba(30,30,40,.05));
    border-radius:3px;
  }
  .contact{
    position:absolute;right:62px;bottom:150px;
    text-align:right;font-size:9px;line-height:1.45;
  }
  .contact-line{display:flex;justify-content:flex-end;align-items:center;gap:4px;}
  .contact-line svg{width:8px;height:8px;fill:var(--accent);}
</style>
</head>
<body>
  <main class="letterhead">
    <header class="brand">
      <span class="brand-mark"></span>
      <span class="brand-name">Marwick Law</span>
    </header>
    <div class="brand-rule"></div>

    <section class="letter">
      <p class="salutation">Dear Mr. Ellison,</p>
      <p class="body">Lorem ipsum dolor sit amet, consectetur adipiscing elit. Donec orci purus, luctus vitae dignissim eu, iaculis sed purus. Vivamus faucibus, ipsum nec aliquet viverra, leo mauris condimentum ligula, sit amet sagittis enim ligula quis arcu. Nam egestas tortor id nisl porttitor mattis. In tortor ante, ultricies in suscipit a, tempus non massa. Vivamus et auctor mi. Fusce vel massa nulla. Phasellus nec eros mauris, et scelerisque orci.</p>
      <p class="body">Donec malesuada orci vitae nulla accumsan porta a id massa. Quisque accumsan iaculis magna sit amet fringilla. Maecenas consequat, magna eget tincidunt semper, odio nibh rutrum mi, id feugiat ante nisl eu risus. Vestibulum nunc orci, rhoncus a placerat in, ultricies in mi. Cras mattis varius eros, vel fringilla nisi suscipit eget. Quisque scelerisque sagittis nulla at porttitor.</p>
      <p class="body">Sed id augue vitae urna euismod commodo aliquet a quam. Pellentesque arcu velit, cursus et malesuada ut, consequat et diam. Nullam erat sem, rhoncus id ullamcorper vitae, rhoncus et arcu. In ultricies ultricies nulla, ut rutrum nisl iaculis at. Donec eu magna a metus ornare faucibus. Fusce aliquet faucibus ultricies. Morbi semper, est id tincidunt gravida, sem arcu adipiscing lacus, ac bibendum nulla leo eu purus. Quisque nec diam sed risus consectetur accumsan quis quis nibh. Vestibulum id purus lorem.</p>
      <p class="closing">Sincerely,</p>
      <span class="signature" role="img" aria-label="Handwritten signature of the sender"></span>
    </section>

    <address class="contact">
      <div>1475 Calloway Street</div>
      <div>Suite 210</div>
      <div>Houston, Texas 77041</div>
      <div class="contact-line">832-361-9027
        <svg viewBox="0 0 10 10" aria-hidden="true"><path d="M2 0.5h2l0.8 2.4-1.3 1a5 5 0 0 0 2.6 2.6l1-1.3 2.4.8v2a1.5 1.5 0 0 1-1.5 1.5A8.5 8.5 0 0 1 .5 2 1.5 1.5 0 0 1 2 .5z"/></svg>
      </div>
      <div class="contact-line">832-614-7359
        <svg viewBox="0 0 10 10" aria-hidden="true"><path d="M2.5 0.5h5v2.5h-5z M1 3.5h8a1 1 0 0 1 1 1v4H0v-4a1 1 0 0 1 1-1z"/></svg>
      </div>
    </address>
  </main>
</body>
</html>
```